Real Estate Company Looking for Business Card Designs for 3 Executives

Hello!
Thanks so much for considering our project! We are a real estate investment company located in Edmonton, Alberta called Bellhaven Group of Companies. We invest/develop both commercial and residential real estate and are looking to create 3 DOUBLE-SIDED business cards for 3 top executives in the company! (for some reason it won't let us select the double-sided option, but yes, the cards are double sided and would be happy to tip extra)

We have certain guidelines that we want our business cards to for sure follow - the back of the Business card has to be the Black Background Version of the Logo which has already been designed and linked as a file (first file). We want the entire back of the card to simply just be the black background logo. In terms of the front of the card, would like to see a smaller version of the white background logo (linked as the second file) in the top left hand corner - of course, feel free to get creative and we can make revisions together along the way! and Then after that, just text. We want the card to be sharp, clean, easy on the eyes and highly professional looking. We would like the card to include the Full name of the Company (Bellhaven Group of Companies), Name of the Person, Title, Phone, Email. If possible please provide the front part of the card for 3 people:

1) Bellhaven Group of Companies, Liora Quenby, Chief Financial Officer, 780-555-0142, lioraquenby@bellhavengroup.example

2) Bellhaven Group of Companies, Tobias Quenby, Chief Executive Officer, 780-555-0187, tobiasquenby@bellhavengroup.example

3) Bellhaven Group of Companies, Rui Delcourt, Chief Operations Officer, 587-555-0163, ruidelcourt@bellhavengroup.example

Thank you so much for considering our project & we look forward to seeing your designs!

```html
<!DOCTYPE html>
<html lang="en">
<head>
<meta charset="utf-8">
<title>Bellhaven Business Card</title>
<link href="https://fonts.googleapis.com/css2?family=Arimo:wght@400;700&display=swap" rel="stylesheet">
<style>
  :root {
    --ink: #0b0b0b;
    --paper: #ffffff;
    --stage: #2b2b2b;
    --rule: #d4d4d4;
    --mist: #ececec;
    --frost: #f2f7f8;
    --night: #141414;
  }
  * { box-sizing: border-box; margin: 0; padding: 0; }
  html, body { width: 1200px; height: 866px; overflow: hidden; }
  body {
    background: var(--stage);
    font-family: "Arimo", Arial, sans-serif;
    display: flex;
    flex-direction: column;
    align-items: center;
    justify-content: center;
    gap: 40px;
  }
  .card {
    position: relative;
    width: 665px;
    height: 380px;
    overflow: hidden;
    box-shadow: 0 10px 24px rgba(0,0,0,.45);
  }
  /* front */
  .card--front { background: var(--paper); color: var(--ink); }
  .forest-fade {
    position: absolute;
    left: 0; top: 0;
    width: 330px; height: 300px;
    background: linear-gradient(135deg, var(--mist) 0%, rgba(236,236,236,.5) 45%, rgba(255,255,255,0) 80%);
  }
  .contact {
    position: absolute;
    left: 40px;
    top: 150px;
  }
  .contact__name {
    font-weight: 700;
    font-size: 25px;
    letter-spacing: .5px;
    text-transform: uppercase;
  }
  .contact__title {
    font-size: 17px;
    margin-top: 2px;
  }
  .contact__line {
    display: flex;
    align-items: center;
    gap: 8px;
    font-size: 16px;
    margin-top: 6px;
  }
  .contact__line:first-of-type { margin-top: 16px; }
  .contact__line svg { width: 14px; height: 14px; flex: none; }
  .divider {
    position: absolute;
    left: 40px; right: 40px;
    top: 292px;
    height: 1px;
    background: var(--rule);
  }
  .wordmark {
    position: absolute;
    font-weight: 700;
    text-transform: uppercase;
    white-space: nowrap;
  }
  .card--front .wordmark {
    left: 390px; top: 170px;
    font-size: 30px;
    letter-spacing: 6px;
  }
  .footer-band {
    position: absolute;
    left: 0; bottom: 0;
    width: 665px; height: 52px;
  }
  .footer-band__url {
    position: absolute;
    right: 34px; bottom: 14px;
    color: var(--paper);
    font-weight: 700;
    font-size: 16px;
    letter-spacing: .3px;
  }
  /* back */
  .card--back { background: var(--ink); color: var(--frost); }
  .forest-shade {
    position: absolute;
    left: 0; top: 0;
    width: 100%; height: 100%;
    background: linear-gradient(90deg, var(--night) 0%, #1c1c1c 35%, var(--ink) 60%);
  }
  .card--back .wordmark {
    left: 50%; top: 50%;
    transform: translate(-50%, -50%);
    font-size: 44px;
    letter-spacing: 12px;
  }
</style>
</head>
<body>

  <section class="card card--front" aria-label="Card front">
    <div class="forest-fade" role="img" aria-label="Faint pale forest of tall tree trunks"></div>

    <div class="contact">
      <p class="contact__name">Liora Quenby</p>
      <p class="contact__title">Chief Financial Officer</p>
      <p class="contact__line">
        <svg viewBox="0 0 16 16" aria-hidden="true"><path d="M3.6 1.5l2.3 2.6-1.3 1.6c.9 2 2.6 3.7 4.6 4.6l1.6-1.3 2.7 2.3-1.3 2.2C7.2 14.7 1.3 8.8 1.4 3z" fill="#0b0b0b"/></svg>
        780-555-0142
      </p>
      <p class="contact__line">
        <svg viewBox="0 0 16 16" aria-hidden="true"><rect x="1" y="3" width="14" height="10" fill="#0b0b0b"/><path d="M1 3l7 6 7-6" stroke="#fff" stroke-width="1.2" fill="none"/></svg>
        lioraquenby@bellhavengroup.example
      </p>
    </div>

    <div class="divider"></div>

    <p class="wordmark">Bellhaven</p>

    <div class="footer-band">
      <svg width="665" height="52" viewBox="0 0 665 52" aria-hidden="true">
        <path d="M0 40 H250 C268 40 262 6 290 6 H665 V52 H0 Z" fill="#0b0b0b"/>
        <path d="M0 34 H248 C262 34 258 0 286 0" stroke="#0b0b0b" stroke-width="1.5" fill="none"/>
      </svg>
      <span class="footer-band__url">www.bellhavengroup.example</span>
    </div>
  </section>

  <section class="card card--back" aria-label="Card back">
    <div class="forest-shade" role="img" aria-label="Dark forest of tree trunks in deep shadow"></div>
    <p class="wordmark">Bellhaven</p>
  </section>

</body>
</html>
```